Charity Initiative needs a WebPage design

We need a web design for charity initiative by two young guys riding their bikes around Australia to support HarbourLight which helps people with depression and anxiety. Full brief and requirements are attached in the PDF and word document. We have the logo already done and attached. Website will be done in Wordpress and need to get Donations, display current donations, show live Video feed, GPS tracker, Blogs etc and also ability to sell merchandise later

Target Market(s)

Sponsors, Business, Young People

Number of Pages Required

4 page

Font styles to use
Serif
Sans Serif
Decorative
Script

Requirements
Must have
• As per Brief and also Donation status etc
Nice to have
• Please check my logo and read the Bried

```html
<!DOCTYPE html>
<html lang="en">
<head>
<meta charset="utf-8">
<title>Long Road Run</title>
<link href="https://fonts.googleapis.com/css2?family=Oswald:wght@300;400&family=Open+Sans:wght@400;600;700&display=swap" rel="stylesheet">
<style>
:root{
  --pink:#e0195b;
  --pink-soft:#f08aa9;
  --teal:#3aa89f;
  --ink:#333;
  --muted:#666;
  --light:#ececec;
  --line:#d8d8d8;
  --backdrop-a:#c99a2e;
  --backdrop-b:#b8782a;
  --white:#fff;
}
*{margin:0;padding:0;box-sizing:border-box}
html,body{width:678px;height:1200px;overflow:hidden}
body{background:radial-gradient(circle at 50% 40%,var(--backdrop-a),var(--backdrop-b));font-family:"Open Sans",sans-serif;color:var(--ink);position:relative}
.page{position:absolute;left:54px;top:0;width:568px;height:1200px;background:var(--white);border-top:3px solid var(--pink)}
.abs{position:absolute}
.heading{font-family:"Oswald",sans-serif;font-weight:400;text-transform:uppercase;color:var(--ink)}
.heading em{font-style:normal;color:var(--pink)}

/* header */
.brand{left:12px;top:22px;display:flex;align-items:center;gap:6px;font-family:"Oswald",sans-serif;font-size:19px;color:var(--pink);text-transform:uppercase}
.brand i{width:14px;height:14px;border-radius:50%;background:var(--pink);display:block}
.phone{left:391px;top:10px;font-family:"Oswald",sans-serif;font-weight:300;font-size:10px;color:#e89a1c;display:flex;align-items:center;gap:5px}
.donate-top{left:480px;top:0;width:67px;height:27px;background:var(--pink);color:#fff;font-family:"Oswald",sans-serif;font-size:9.5px;display:flex;align-items:center;justify-content:center}
.nav{left:172px;top:40px;display:flex;font-family:"Oswald",sans-serif;font-size:9.5px;text-transform:uppercase}
.nav a{color:var(--ink);text-decoration:none;height:22px;line-height:22px;padding:0 8px;margin-right:6px}
.nav a.active{background:var(--teal);color:#fff}
.search{left:435px;top:41px;width:117px;height:20px;border:1px solid #999;font-family:"Oswald",sans-serif;font-size:7px;color:#555;display:flex;align-items:center;gap:5px;padding-left:8px}

/* hero */
.hero{left:0;top:75px;width:568px;height:258px;background:linear-gradient(160deg,#e9d6bb 0%,#b89a7c 45%,#6d5a4c 100%)}
.hero-caption{left:63px;top:229px;width:251px;height:50px;background:rgba(255,255,255,.85);color:var(--pink);font-family:"Oswald",sans-serif;font-size:15px;line-height:16px;padding:8px 12px;text-transform:uppercase}
.arrow{width:18px;height:18px;border-radius:50%;background:#333;top:194px}

/* middle */
.video{left:18px;top:357px;width:288px;height:173px;background:#eee;padding:8px}
.video-frame{width:272px;height:142px;background:linear-gradient(160deg,#b7c1c4,#5f6263);position:relative}
.video-bar{height:15px;background:#fff;font-size:4.5px;display:flex;align-items:center;gap:8px;padding:0 8px;color:#555}
.video-bar .track{flex:1;height:2px;background:#ccc;position:relative}
.video-bar .track::after{content:"";position:absolute;left:0;top:0;width:45%;height:2px;background:var(--pink)}
.videos-title{left:18px;top:544px;font-size:19px}
.videos-text{left:18px;top:569px;width:270px;font-size:6.3px;line-height:12.5px;color:var(--ink)}
.btn-teal{left:18px;top:613px;width:69px;height:21px;background:var(--teal);color:#fff;font-family:"Oswald",sans-serif;font-size:7.5px;display:flex;align-items:center;justify-content:center}
.donations-title{left:331px;top:356px;font-size:19px;line-height:24px;width:180px}
.callout{left:384px;width:130px;border:1px solid var(--line);border-radius:3px;font-size:8.5px;color:var(--ink);padding:0 8px;display:flex;flex-direction:column;justify-content:center}
.callout small{font-size:5.5px;font-style:italic;margin-top:3px}
.callout::before{content:"";position:absolute;left:-6px;top:50%;margin-top:-5px;border:5px solid transparent;border-right-color:#ddd;border-left:0}

/* blog */
.blog{left:0;top:670px;width:568px;height:266px;background:var(--light)}
.blog-title{left:0;width:568px;top:688px;text-align:center;font-size:17px}
.card{top:724px;height:186px;background:#fff;border:1px solid #ddd;padding:2px}
.card-img{height:92px}
.card h3{font-size:6.5px;font-weight:600;margin:12px 4px 5px;text-transform:uppercase}
.card .meta{font-size:6px;color:#444;margin:0 4px 4px;display:flex;gap:6px;align-items:center}
.card .meta b{display:inline-block;width:6px;height:6px;background:#444;border-radius:1px}
.card p{font-size:6px;line-height:12px;margin:0 4px;text-align:justify}

/* newsletter */
.newsletter{left:0;top:938px;width:568px;height:52px;background:var(--pink);color:#fff}
.news-label{left:52px;top:12px;font-family:"Oswald",sans-serif;text-transform:uppercase}
.news-label small{display:block;font-size:6.5px;line-height:8px}
.news-label span{font-size:14px;line-height:18px}
.news-input{left:138px;top:14px;width:345px;height:24px;background:#fff;color:#777;font-family:"Oswald",sans-serif;font-weight:300;font-size:8px;display:flex;align-items:center;padding-left:13px}
.news-btn{left:493px;top:14px;width:64px;height:24px;border:1.5px solid #fff;font-family:"Oswald",sans-serif;font-size:7.5px;display:flex;align-items:center;justify-content:center}

/* footer info */
.foot-title{font-family:"Oswald",sans-serif;color:var(--pink);font-size:12px;text-transform:uppercase;top:1013px}
.map{left:14px;top:1032px;width:234px;height:118px;background:linear-gradient(135deg,#e9e1a8,#cfc9b2 60%,#8fb3cf);border:1px solid #bbb}
.links{list-style:none;font-size:6.3px;color:var(--ink)}
.links li{height:17.5px;padding-left:9px;position:relative}
.links li::before{content:"›";position:absolute;left:0;top:-1px;font-size:8px}
.partner{left:458px;top:1066px;display:flex;align-items:center;gap:6px;font-family:"Open Sans",sans-serif;font-size:9px;font-weight:600;color:#3a7fc4}
.partner i{width:12px;height:12px;background:#3a7fc4;display:block}

/* bottom bar */
.bottom{left:0;top:1172px;width:568px;height:28px;background:var(--pink);color:#fff;font-size:6.5px}
.copyright{left:14px;top:10px}
.social{left:401px;top:6px;display:flex;align-items:center;gap:5px}
.social i{width:16px;height:16px;border-radius:50%;background:#fff;display:block}
</style>
</head>
<body>
<div class="page">
  <header>
    <div class="abs brand"><i></i>Long Road Run</div>
    <div class="abs phone">
      <svg width="14" height="14" viewBox="0 0 14 14"><circle cx="7" cy="7" r="6.2" fill="none" stroke="#e0195b" stroke-width="1"/><path d="M4.6 4c.6-.4 1 0 1.3.7l.3.7c.1.3 0 .6-.3.8l-.3.2c.3.8.9 1.5 1.7 1.9l.3-.3c.2-.2.5-.3.8-.1l.7.4c.6.3.9.8.5 1.3-.6.7-1.5.8-2.5.2-1.5-.9-2.6-2.3-3-3.7-.2-.9.1-1.7.5-2.1z" fill="#e0195b"/></svg>
      +1 555 010 2040
    </div>
    <div class="abs donate-top">DONATE NOW</div>
    <nav class="abs nav">
      <a class="active">Home</a><a>Blog</a><a>Progress</a><a>Contact</a><a>Donate</a>
    </nav>
    <div class="abs search">
      <svg width="7" height="7" viewBox="0 0 7 7"><circle cx="3" cy="3" r="2.2" fill="none" stroke="#333"/><path d="M4.6 4.6L6.6 6.6" stroke="#333"/></svg>
      SEARCH
    </div>
  </header>

  <section>
    <div class="abs hero" role="img" aria-label="Two riders on motorbikes bumping fists on a sunlit road"></div>
    <div class="abs hero-caption">Two young guys riding their bikes around Australia</div>
    <svg class="abs arrow" style="left:24px" viewBox="0 0 18 18"><path d="M10.5 5L6.5 9l4 4" stroke="#fff" stroke-width="1.6" fill="none"/></svg>
    <svg class="abs arrow" style="left:529px" viewBox="0 0 18 18"><path d="M7.5 5l4 4-4 4" stroke="#fff" stroke-width="1.6" fill="none"/></svg>
  </section>

  <section>
    <div class="abs video">
      <div class="video-frame" role="img" aria-label="Video still of two riders greeting on motorbikes">
        <svg class="abs" style="left:121px;top:56px" width="30" height="30" viewBox="0 0 30 30"><circle cx="15" cy="15" r="14" fill="rgba(80,80,80,.55)" stroke="#ddd"/><path d="M12 9l9 6-9 6z" fill="#eee"/></svg>
      </div>
      <div class="video-bar"><span>▶</span><span>00:00/05:03</span><div class="track"></div><span>◀)</span></div>
    </div>
    <h2 class="abs heading videos-title"><em>Latest</em> Videos</h2>
    <p class="abs videos-text">Whether you're a novice or an experienced caravan holiday-maker, our towing e-book with essential safety.Whether you're a novice or an experienced caravan holiday-maker, our towing e-book with essential safety</p>
    <div class="abs btn-teal">VIEW MORE INFO</div>

    <h2 class="abs heading donations-title"><em>Donations help</em> to purchase</h2>
    <svg class="abs" style="left:326px;top:408px" width="40" height="226" viewBox="0 0 40 226">
      <path d="M8 12a9 9 0 0 1 18 0v170a16 16 0 1 1-18 0z" fill="#fff" stroke="#111" stroke-width="2"/>
      <rect x="12" y="54" width="10" height="140" fill="url(#merc)"/>
      <circle cx="17" cy="197" r="12" fill="#c4164f"/>
      <defs><linearGradient id="merc" x1="0" y1="0" x2="0" y2="1"><stop offset="0" stop-color="#f5a1bc"/><stop offset="1" stop-color="#c4164f"/></linearGradient></defs>
      <g stroke="#111" stroke-width="1">
        <path d="M26 16h7M26 29h5M26 42h7M26 55h5M26 68h7M26 81h5M26 94h7M26 107h5M26 120h7M26 133h5M26 146h7M26 159h5M26 172h7"/>
      </g>
    </svg>
    <div class="abs callout" style="top:433px;height:48px">$5000 Equipment<small>Our Goal</small></div>
    <div class="abs callout" style="top:550px;height:28px">We are here so far in 2016</div>
    <div class="abs callout" style="top:588px;height:29px">$5 Minor Purchase</div>
  </section>

  <section>
    <div class="abs blog"></div>
    <h2 class="abs heading blog-title"><em>Latest</em> Blog</h2>
    <article class="abs card" style="left:11px;width:130px">
      <div class="card-img" style="background:linear-gradient(180deg,#9fb8d6,#8b8370 55%,#6d6b66)" role="img" aria-label="Rider on a mountain road"></div>
      <h3>At vero eos et accusamus</h3>
      <div class="meta"><b></b>27 March 2014 <b></b>120</div>
      <p>Lorem Ipsum is simply dummy text of the printing and typesetting industry. Lorem Ipsumthe industry's Lorem Ipsum is simply dummy</p>
    </article>
    <article class="abs card" style="left:150px;width:129px">
      <div class="card-img" style="background:linear-gradient(160deg,#f2d9a6,#9c7a55 55%,#4d3f33)" role="img" aria-label="Rider on a road at sunset"></div>
      <h3>Iusto odio dignissimos</h3>
      <div class="meta"><b></b>27 March 2014 <b></b>120</div>
      <p>Lorem Ipsum is simply dummy text of the printing and typesetting industry. Lorem Ipsumthe industry's Lorem Ipsum is simply dummy</p>
    </article>
    <article class="abs card" style="left:288px;width:130px">
      <div class="card-img" style="background:linear-gradient(180deg,#a9c3dd,#6f8a5a 50%,#6c6b68)" role="img" aria-label="Two riders on a tree-lined road"></div>
      <h3>Dignissimos ducimus qui</h3>
      <div class="meta"><b></b>27 March 2014 <b></b>120</div>
      <p>Lorem Ipsum is simply dummy text of the printing and typesetting industry. Lorem Ipsumthe industry's Lorem Ipsum is simply dummy</p>
    </article>
    <article class="abs card" style="left:427px;width:130px">
      <div class="card-img" style="background:linear-gradient(180deg,#b9c9d6,#6e7f60 45%,#5a5855)" role="img" aria-label="Two riders shaking hands on motorbikes"></div>
      <h3>Blanditiis praesentium</h3>
      <div class="meta"><b></b>27 March 2014 <b></b>120</div>
      <p>Lorem Ipsum is simply dummy text of the printing and typesetting industry. Lorem Ipsumthe industry's Lorem Ipsum is simply dummy</p>
    </article>
  </section>

  <section class="abs newsletter">
    <svg class="abs" style="left:16px;top:15px" width="27" height="21" viewBox="0 0 27 21"><path d="M2 7l13-6 10 8-12 10z" fill="#fff"/><path d="M2 7l11 4 12-2" fill="none" stroke="#e0195b" stroke-width="1.2"/></svg>
    <div class="abs news-label"><small>Free weekly</small><span>Newsletter</span></div>
    <div class="abs news-input">ENTER YOUR EMAIL ADDRESS...</div>
    <div class="abs news-btn">SUBSCRIBE</div>
  </section>

  <section>
    <h4 class="abs foot-title" style="left:14px">Location Map</h4>
    <div class="abs map" role="img" aria-label="Street map with the riding route marked"></div>
    <h4 class="abs foot-title" style="left:278px">Popular</h4>
    <ul class="abs links" style="left:278px;top:1041px">
      <li>Finibus Bonorum et Malorum</li>
      <li>Sed ut perspiciatis unde omnis ister</li>
      <li>Natus error sit voluptatem accusantium</li>
      <li>Doloremque laudantium, totam</li>
      <li>Quae ab illo inventore veritatis</li>
    </ul>
    <h4 class="abs foot-title" style="left:450px">Recommended</h4>
    <ul class="abs links" style="left:450px;top:1041px"><li>Magni dolores eos qui</li></ul>
    <div class="abs partner"><i></i>HarbourLight</div>
  </section>

  <footer class="abs bottom">
    <div class="abs copyright">© 2016 longroadrun. All Rights Reserved</div>
    <div class="abs social"><span>Connect With Us :</span><i></i><i></i><i></i><i></i><i></i></div>
  </footer>
</div>
</body>
</html>
```